Promotional Ad/Flyer - Brakko Leasing

A division of our company, Brakko Leasing (brakko-leasing.example) is celebrating its 1-year anniversary in September and we would like to run a promotion. I am looking to have a promotional ad/flyer made-up for email mailings and LinkedIn posts and possibly have on our site. Have plenty of product photos to share if needed, not a prerequisite to use our product in the ad but open to it. Can also be cool graphics as well. We want to capture the viewers attention with the 30 DAYS FREE! The message is simple:
We are celebrating our 1-Year Anniversary by offering a Special Peak-Season Promotion!

FREE RENTALS for 30 days with a minimum 30-Day rental!

Valid from Sep. 1 - Dec. 31 & while supplies last.

Please contact our sales department for more details.

Email: quotes@brakko-leasing.example
Phone: +1-555-284-9317

```html
<!DOCTYPE html>
<html lang="en">
<head>
<meta charset="utf-8">
<title>Brakko Leasing – 1 Year Anniversary Promotion</title>
<link rel="stylesheet" href="https://fonts.googleapis.com/css2?family=Anton&family=Cinzel:wght@600&family=Montserrat:wght@600;700&family=Tinos:ital,wght@0,700;1,700&display=swap">
<style>
  :root {
    --stage: #3a3a3a;
    --night: #120910;
    --night-warm: #2a1606;
    --gold: #d9a531;
    --gold-light: #f6d77a;
    --gold-deep: #9b6a12;
    --orange: #f46a06;
    --ribbon: #8c1414;
    --ink: #111111;
    --logo-ink: #2b2d33;
    --blue: #3657b8;
    --white: #ffffff;
    --grey-text: #6b6b6b;
  }
  * { box-sizing: border-box; margin: 0; padding: 0; }
  html, body { width: 990px; height: 1200px; overflow: hidden; }
  body { background: var(--stage); position: relative; }

  .flyer {
    position: absolute;
    left: 31px; top: 0;
    width: 1198px; height: 1551px;
    transform: scale(0.7737);
    transform-origin: 0 0;
    overflow: hidden;
    background: var(--night);
  }
  .flyer > * { position: absolute; }

  .sparkle-backdrop {
    inset: 0;
    background:
      radial-gradient(ellipse 80% 30% at 50% 72%, rgba(240,180,40,.75), rgba(200,130,20,.35) 55%, transparent 80%),
      linear-gradient(180deg, var(--night) 0%, #1a0d0a 40%, var(--night-warm) 58%, #7a5210 75%, #3a2508 92%);
  }

  .anniversary-emblem {
    left: 365px; top: 170px; width: 470px; height: 430px;
    border-radius: 50%;
    background: radial-gradient(ellipse at center, rgba(217,165,49,.28), rgba(155,106,18,.12) 55%, transparent 72%);
  }

  .arc-heading { left: 0; top: 0; width: 1198px; height: 600px; }
  .arc-heading text {
    font-family: "Tinos", serif; font-weight: 700; font-size: 50px;
    fill: var(--white); letter-spacing: 2px;
  }

  .year-number {
    left: 0; width: 1198px; top: 150px; text-align: center;
    font-family: "Tinos", serif; font-weight: 700; font-size: 290px; line-height: 1;
    background: linear-gradient(180deg, var(--gold-light), var(--gold) 55%, var(--gold-deep));
    -webkit-background-clip: text; background-clip: text; color: transparent;
  }
  .year-label {
    left: 0; width: 1198px; top: 408px; text-align: center;
    font-family: "Cinzel", serif; font-weight: 600; font-size: 52px; line-height: 1;
    color: var(--gold);
  }
  .ribbon {
    left: 412px; top: 470px; width: 374px; height: 80px;
    border-radius: 40px;
    background: linear-gradient(180deg, #b11d1d, var(--ribbon) 70%, #5c0b0b);
    display: flex; align-items: center; justify-content: center;
    font-family: "Montserrat", sans-serif; font-weight: 600; font-size: 34px;
    color: var(--gold-light); letter-spacing: 1px;
  }

  .intro-line {
    left: 0; width: 1198px; top: 605px; text-align: center;
    font-family: "Tinos", serif; font-style: italic; font-weight: 700; font-size: 46px;
    color: var(--white); text-shadow: 2px 2px 3px rgba(0,0,0,.7);
  }
  .promo-title {
    left: 0; width: 1198px; top: 668px; text-align: center;
    font-family: "Tinos", serif; font-weight: 700; font-size: 68px;
    color: var(--white); text-shadow: 3px 3px 4px rgba(0,0,0,.7);
  }

  .headline {
    left: 0; width: 1198px; top: 780px; text-align: center;
    font-family: "Anton", sans-serif; font-size: 180px; line-height: 1.02;
    letter-spacing: 0;
    color: var(--gold);
    -webkit-text-stroke: 5px var(--white);
    paint-order: stroke fill;
    text-shadow: 6px 8px 0 rgba(40,25,5,.85);
  }

  .offer-bar {
    left: 127px; top: 990px; width: 944px; height: 64px;
    background: var(--orange);
    display: flex; align-items: center; justify-content: center;
    font-family: "Montserrat", sans-serif; font-weight: 700; font-size: 28px; color: var(--white);
  }
  .offer-frame {
    left: 127px; top: 1054px; width: 944px; height: 114px;
    border: 2px solid var(--orange); border-top: none;
  }
  .validity {
    left: 242px; top: 1068px; width: 714px; height: 64px;
    background: var(--ink);
    display: flex; align-items: center; justify-content: center;
    font-family: "Montserrat", sans-serif; font-weight: 700; font-size: 46px; color: var(--white);
  }
  .validity .dates { color: var(--orange); margin-left: 14px; }
  .supply-note {
    left: 405px; top: 1143px; width: 388px; height: 50px;
    background: var(--ink);
    display: flex; align-items: center; justify-content: center;
    font-family: "Montserrat", sans-serif; font-weight: 700; font-size: 28px; color: var(--white);
  }

  .footer-curve { left: 0; top: 1210px; width: 1198px; height: 220px; }

  .brand {
    left: 0; width: 1198px; top: 1282px;
    display: flex; align-items: center; justify-content: center; gap: 22px;
  }
  .brand-square { width: 56px; height: 56px; background: var(--blue); }
  .brand-name {
    font-family: "Montserrat", sans-serif; font-weight: 700; font-size: 62px;
    color: var(--logo-ink); line-height: 1;
  }
  .brand-tagline {
    left: 532px; width: 300px; top: 1360px; text-align: right;
    font-family: "Montserrat", sans-serif; font-weight: 600; font-size: 11px;
    color: var(--grey-text); letter-spacing: 1px;
  }

  .contact-band { left: 0; top: 1415px; width: 1198px; height: 136px; background: var(--blue); }
  .contact-bar {
    left: 128px; top: 1385px; width: 942px; height: 58px;
    background: var(--orange);
    display: flex; align-items: center; justify-content: center;
    font-family: "Montserrat", sans-serif; font-weight: 700; font-size: 25px;
    color: var(--white); letter-spacing: .5px;
  }
  .contact-list {
    left: 0; width: 1198px; top: 1462px; height: 44px;
    list-style: none;
    display: flex; align-items: center; justify-content: center;
    font-family: "Montserrat", sans-serif; font-weight: 700; font-size: 21px; color: var(--white);
  }
  .contact-list li { display: flex; align-items: center; gap: 9px; }
  .contact-list li + li::before {
    content: ""; width: 3px; height: 30px; background: var(--orange); margin: 0 18px 0 10px;
  }
  .contact-list svg { width: 22px; height: 22px; fill: none; stroke: var(--white); stroke-width: 1.8; }
</style>
</head>
<body>
<main class="flyer">
  <div class="sparkle-backdrop" role="img" aria-label="Dark backdrop with glowing gold bokeh sparkles"></div>

  <div class="anniversary-emblem" role="img" aria-label="Gold laurel wreath framing the anniversary number"></div>

  <svg class="arc-heading" viewBox="0 0 1198 600">
    <defs>
      <path id="arc-path" d="M 299 430 A 300 300 0 0 1 899 430"/>
    </defs>
    <text><textPath href="#arc-path" startOffset="50%" text-anchor="middle">WE ARE CELEBRATING OUR</textPath></text>
  </svg>

  <div class="year-number">1</div>
  <div class="year-label">YEAR</div>
  <div class="ribbon">ANNIVERSARY</div>

  <p class="intro-line">by offering a</p>
  <h2 class="promo-title">Special Peak-Season Promotion!</h2>

  <h1 class="headline">30 DAYS FREE!</h1>

  <div class="offer-frame"></div>
  <p class="offer-bar">FREE RENTALS for 30 days with a minimum 30-Day rental!</p>
  <p class="validity">VALID FROM <span class="dates">SEP. 1 - DEC. 31</span></p>
  <p class="supply-note">WHILE SUPPLIES LAST.</p>

  <svg class="footer-curve" viewBox="0 0 1198 220" preserveAspectRatio="none">
    <path d="M0 80 Q599 -60 1198 80 L1198 220 L0 220 Z" fill="#ffffff"/>
  </svg>

  <div class="brand">
    <span class="brand-square"></span>
    <span class="brand-name">BRAKKO LEASING</span>
  </div>
  <p class="brand-tagline">BRAKKO-LEASING.EXAMPLE | BY NORVANE</p>

  <div class="contact-band"></div>
  <p class="contact-bar">PLEASE CONTACT OUR SALES DEPARTMENT FOR MORE DETAILS.</p>
  <ul class="contact-list">
    <li>
      <svg viewBox="0 0 24 24"><rect x="2" y="5" width="20" height="14"/><path d="M2 5 L12 13 L22 5"/></svg>
      quotes@brakko-leasing.example
    </li>
    <li>
      <svg viewBox="0 0 24 24"><circle cx="12" cy="12" r="10"/><path d="M8.5 7 L10.5 7 L11 10 L9.8 11 Q11 13.5 13 14.2 L14 13 L17 13.5 L17 15.5 Q11 17 7.5 9 Z"/></svg>
      +1-555-284-9317
    </li>
    <li>
      <svg viewBox="0 0 24 24"><circle cx="12" cy="12" r="10"/><ellipse cx="12" cy="12" rx="4.5" ry="10"/><path d="M2 12 H22 M4 7 H20 M4 17 H20"/></svg>
      brakko-leasing.example
    </li>
  </ul>
</main>
</body>
</html>
```